Looking for a cool & simple business-card-design for digital agency

Hi!

We are a web agency that offers Reputation Management, Vextor & Seo Services and software development. We like cool things, we like innovative styles.

We have uploaded our logo.

Project Deadline Extended Reason: Client does not want any designs with the colorful logo. Please send us submissions ONLY with the blac and white logo. What the client would like to see:1) Back of the card: is a silver logo on a black background2) front of the card with all the data, please use white background and black logo thank you Added Friday, May 8, 2015

Industry/Entity Type

Software

```html
<!DOCTYPE html>
<html lang="en">
<head>
<meta charset="utf-8">
<title>Netquill AG – Business Card</title>
<link rel="stylesheet" href="https://fonts.googleapis.com/css2?family=Lato:wght@400;700;900&display=swap">
<style>
  :root {
    --stage: #e9e6e2;
    --card-black: #050505;
    --card-white: #ffffff;
    --ink: #1c1c1c;
    --silver: #c9c9c9;
    --paper-text: #ffffff;
    --rule: #2a2a2a;
  }
  * { box-sizing: border-box; margin: 0; padding: 0; }
  html, body {
    width: 1200px; height: 905px; overflow: hidden;
    background: var(--stage);
    font-family: "Lato", sans-serif;
  }
  .canvas { position: relative; width: 1200px; height: 905px; }
  .card {
    position: absolute; width: 640px; height: 365px;
    box-shadow: 0 10px 24px rgba(0,0,0,.25);
  }
  /* back side */
  .card-back { left: 100px; top: 70px; background: var(--card-black); }
  .card-back .brand {
    position: absolute; left: 90px; top: 110px;
    display: flex; align-items: center; gap: 16px;
    color: var(--silver); font-weight: 900; font-size: 46px; letter-spacing: 1px;
  }
  .brand-mark { width: 34px; height: 34px; background: currentColor; }
  .card-back .services {
    position: absolute; left: 260px; top: 190px;
    color: var(--paper-text); font-weight: 700; font-size: 21px; line-height: 1.3;
    list-style: none;
  }
  /* front side */
  .card-front { left: 460px; top: 470px; background: var(--card-white); color: var(--ink); }
  .card-front .brand {
    position: absolute; left: 300px; top: 42px;
    display: flex; align-items: center; gap: 10px;
    font-weight: 900; font-size: 30px; letter-spacing: .5px;
  }
  .card-front .brand .brand-mark { width: 20px; height: 20px; }
  .card-front .block-mark {
    position: absolute; left: 70px; top: 140px; width: 150px; height: 150px;
    background: var(--ink);
  }
  .divider {
    position: absolute; left: 262px; top: 110px; width: 2px; height: 190px;
    background: var(--rule);
  }
  .person { position: absolute; left: 290px; top: 110px; }
  .person-name { font-weight: 900; font-size: 21px; }
  .person-role { font-size: 16px; margin-top: 4px; }
  .contacts { list-style: none; margin-top: 14px; font-size: 18px; }
  .contacts li { display: flex; align-items: center; gap: 8px; line-height: 1.45; }
  .contacts svg { width: 15px; height: 15px; flex: none; fill: var(--ink); }
</style>
</head>
<body>
<main class="canvas">
  <section class="card card-back" aria-label="Card back">
    <div class="brand"><span class="brand-mark"></span>Netquill AG</div>
    <ul class="services">
      <li>Reputation Management</li>
      <li>Vextor &amp; Seo Services</li>
      <li>Software development.</li>
    </ul>
  </section>

  <section class="card card-front" aria-label="Card front">
    <div class="brand"><span class="brand-mark"></span>Netquill AG</div>
    <div class="block-mark"></div>
    <div class="divider"></div>
    <div class="person">
      <p class="person-name">Lorin Vale</p>
      <p class="person-role">Director</p>
      <ul class="contacts">
        <li><svg viewBox="0 0 16 16"><path d="M1 6c0-2 3-4 7-4s7 2 7 4l-3 1-1-2H5L4 7zM3 8h10l1 6H2z"/></svg>000 482 7715</li>
        <li><svg viewBox="0 0 16 16"><path d="M4 0h8v16H4zM5.5 2v10h5V2z"/></svg>333 9061 248</li>
        <li><svg viewBox="0 0 16 16"><path d="M0 3h16v10H0zM1.5 4.5 8 9l6.5-4.5z"/></svg>info@netquillag.com</li>
        <li><svg viewBox="0 0 16 16"><circle cx="8" cy="8" r="7.5"/><path d="M1 8h14M8 1v14M3 4h10M3 12h10" stroke="#fff" stroke-width="1" fill="none"/></svg>www.netquillag.com</li>
      </ul>
    </div>
  </section>
</main>
</body>
</html>
```